Vale Linebacker Needs a new website!

We need a four page website for a new company based in San Francisco. We help companies connect better with their clients, employees, and vendors by implementing collaborative technology.
Similar Websites
Mist Rangers - http://www.mistrangers.example/
Skyforthing - http://www.skyforthing.example/ - I don't like the the rotating window or the pictures of people. I like the icons used to go to the next pages.
Color Combos
Blues and Yellows - http://www.huepairings.example/palette-sets/96/HuePairing96.html
We prefer graphics over the actual pictures of people in the header. Pictures of people working together in the text is fine.
Web Page Layout
Index
Cloud Advisory Services
Email Everywhere
CRM Implementation
For detailed copy please see this link https://files.paperhold.example/a/widgetladyla.example/document/d/7KtmPzWqAeRbYcNvHsJgLdFxTuQoIeMnBvCxZaSdFgHj/edit
Industry/Entity Type
It Company

```html
<!DOCTYPE html>
<html lang="en">
<head>
<meta charset="utf-8">
<title>Vale Linebacker</title>
<link rel="stylesheet" href="https://fonts.googleapis.com/css2?family=Roboto:wght@400;500;700&family=Lora:ital@1&display=swap">
<style>
:root{
  --blue:#2563b4;
  --blue-dark:#1d55a3;
  --yellow:#fcd006;
  --text:#444;
  --muted:#777;
  --grey-band:#e6e6e6;
  --footer:#1b1b1b;
  --teal:#21b7a5;
  --white:#fff;
}
*{box-sizing:border-box;margin:0;padding:0}
html,body{width:1200px;height:2161px;overflow:hidden}
body{position:relative;background:var(--white);font-family:"Roboto",Arial,sans-serif;color:var(--text)}
.abs{position:absolute}
.top-rule{left:0;top:0;width:1200px;height:4px;background:var(--blue)}
.brand{left:200px;top:26px;display:flex;align-items:center;gap:12px}
.brand-dot{width:34px;height:34px;border-radius:50%;background:var(--blue)}
.brand-name{font-size:30px;font-weight:700;color:var(--blue)}
.search{left:825px;top:39px;width:175px;height:25px;border:1px solid #bbb;border-radius:3px;font-size:10px;color:#999;padding:6px 8px}
.search svg{position:absolute;right:7px;top:6px}
.nav{left:0;top:92px;width:1200px;height:44px;background:var(--blue)}
.nav a{position:absolute;top:0;height:44px;line-height:44px;color:var(--white);font-size:11px;text-decoration:none;transform:translateX(-50%);white-space:nowrap}
.nav .home{left:200px;width:118px;transform:none;background:var(--yellow);text-align:center}
.hero{left:0;top:136px;width:1200px;height:504px;background:
  radial-gradient(ellipse 240px 170px at 400px 300px,rgba(120,180,230,.45),rgba(120,180,230,0) 100%),
  linear-gradient(90deg,#8a8a8a,#b4b4b4 35%,#9a9a9a 65%,#6e6e6e)}
.arrow{width:34px;height:34px;border-radius:50%;background:#fff;top:342px;box-shadow:0 1px 4px rgba(0,0,0,.3)}
.arrow svg{position:absolute;left:11px;top:10px}
.hero-cards{left:200px;top:438px;width:798px;height:202px;display:flex}
.hero-card{flex:1;background:var(--blue);border-right:1px solid #4a80c8;text-align:center;color:#fff;padding-top:15px}
.hero-card:last-child{border-right:0}
.hero-card .ring{width:70px;height:70px;border-radius:50%;background:#fff;margin:0 auto;display:flex;align-items:center;justify-content:center}
.hero-card h3{color:var(--yellow);font-weight:400;font-size:14px;margin:14px 0 7px}
.hero-card p{font-size:10px;line-height:14px;padding:0 14px}
.hero-card .more{font-size:9.5px;color:var(--yellow);margin-top:5px;display:block}
.dots{left:1058px;top:608px;display:flex;gap:5px}
.dots i{width:10px;height:10px;border-radius:50%;background:#fff;border:1px solid #ccc}
.dots i:first-child{background:#6aaae6}
.title{font-weight:400;color:var(--blue)}
.welcome-title{left:0;width:1200px;top:661px;text-align:center;font-size:25px}
.welcome-text{left:200px;width:800px;top:702px;text-align:center;font-size:10.5px;line-height:19.4px;color:#555}
.btn{width:127px;height:30px;background:var(--yellow);color:#333;font-size:11px;text-align:center;line-height:30px}
.band{left:0;top:869px;width:1200px;height:311px;background:var(--grey-band)}
.what-title{left:200px;top:893px;font-size:24px}
.what-text{left:200px;top:932px;width:790px;font-size:11px;line-height:19px;color:#555}
.checks{left:200px;top:990px;list-style:none}
.checks li{height:29px;font-size:11.5px;color:#333;display:flex;align-items:center;gap:10px}
.laptop{left:565px;top:972px;width:430px;height:208px;background:#d4d4d4;border-radius:14px 14px 0 0;padding:20px 16px 0}
.laptop-screen{width:100%;height:188px;background:#fbfbfb}
.services-title{left:0;width:1200px;top:1208px;text-align:center;font-size:24px}
.services-sub{left:0;width:1200px;top:1243px;text-align:center;font-size:10.5px;color:#555}
.service{top:1287px;width:184px;text-align:center;transform:translateX(-50%)}
.service h4{font-weight:400;color:var(--blue);font-size:14px;margin:16px 0 6px}
.service p{font-size:10px;line-height:14.5px;color:#333}
.service .more{font-size:10px;color:var(--blue)}
.video{left:200px;top:1624px;width:408px;height:220px;background:linear-gradient(180deg,#2b6dc2 0 52px,#f4f4f4 52px 196px,#1f1f1f 196px)}
.testi-title{left:654px;top:1617px;font-size:14px;font-weight:500;color:#2a5e9c}
.tarrow{top:1610px;width:22px;height:20px;border:1px solid #ccc;background:#f5f5f5}
.tarrow svg{position:absolute;left:7px;top:5px}
.testi{left:657px;top:1653px;width:341px;height:192px;background:#f6f6f6}
.avatar{left:685px;top:1669px;width:50px;height:50px;border-radius:50%;background:#b89478;border:2px solid #ddd}
.tname{left:745px;top:1673px;font-size:13px;font-weight:700;color:#222}
.trole{left:746px;top:1694px;font-size:11px;font-style:italic;color:var(--blue)}
.quote{left:728px;top:1746px;width:265px;font-family:"Lora",Georgia,serif;font-style:italic;font-size:12.5px;line-height:21px;color:#555}
.qmark{left:686px;top:1740px;font-family:"Lora",Georgia,serif;font-size:36px;color:#aaa}
.footer{left:0;top:1902px;width:1200px;height:226px;background:var(--footer)}
.fcol{top:1938px;width:200px}
.fcol h5{color:#fff;font-size:11px;font-weight:700;margin-bottom:20px}
.fcol p{color:#666;font-size:10px;line-height:15px}
.fcol ul{list-style:none}
.fcol li{color:#555;font-size:10px;height:28px;line-height:28px;border-bottom:1px solid #2a2a2a;width:170px}
.fdiv{top:1935px;width:1px;height:160px;background:#2a2a2a}
.social{left:890px;top:1963px;display:flex;gap:2px}
.social i{width:19px;height:19px}
.copyright{left:0;top:2128px;width:1200px;height:33px;background:var(--blue);color:#fff;font-size:11px;text-align:center;line-height:33px}
</style>
</head>
<body>
<div class="abs top-rule"></div>

<header>
  <div class="abs brand"><span class="brand-dot"></span><span class="brand-name">Vale Linebacker</span></div>
  <div class="abs search">Select
    <svg width="11" height="11" viewBox="0 0 11 11"><circle cx="4.5" cy="4.5" r="3.3" fill="none" stroke="#333" stroke-width="1.5"/><line x1="7" y1="7" x2="10" y2="10" stroke="#333" stroke-width="1.6"/></svg>
  </div>
  <nav class="abs nav">
    <a class="home" href="#">Home</a>
    <a href="#" style="left:353px">Abou Us</a>
    <a href="#" style="left:482px">Cloud Advisory Services</a>
    <a href="#" style="left:632px">Email Everywhere</a>
    <a href="#" style="left:775px">CRM Implementation</a>
    <a href="#" style="left:905px">Contact Us</a>
  </nav>
</header>

<section class="hero-section">
  <div class="abs hero" role="img" aria-label="Blurred office photograph with an illustration of a blue cloud surrounded by communication tools"></div>
  <div class="abs arrow" style="left:61px"><svg width="10" height="14" viewBox="0 0 10 14"><path d="M8 1 2 7l6 6" fill="none" stroke="#333" stroke-width="2.5"/></svg></div>
  <div class="abs arrow" style="left:1088px"><svg width="10" height="14" viewBox="0 0 10 14"><path d="M2 1l6 6-6 6" fill="none" stroke="#333" stroke-width="2.5"/></svg></div>
  <div class="abs hero-cards">
    <div class="hero-card">
      <div class="ring"><svg width="34" height="38" viewBox="0 0 34 38"><circle cx="17" cy="14" r="11" fill="#222"/><path d="M10 22 6 35l6-3 3 5 2-11M24 22l4 13-6-3-3 5-2-11" fill="#222"/></svg></div>
      <h3>Cloud Advisory</h3>
      <p>Lorem ipsum dolor sit amet, consectetur adipisicing elit, sed do eiusmod tempor incididunt.Lorem ipsum dolor sit amet, consectetur</p>
      <span class="more">Read More +</span>
    </div>
    <div class="hero-card">
      <div class="ring"><svg width="38" height="36" viewBox="0 0 38 36"><circle cx="14" cy="22" r="9" fill="none" stroke="#222" stroke-width="6" stroke-dasharray="4 3"/><circle cx="27" cy="10" r="6" fill="none" stroke="#222" stroke-width="4" stroke-dasharray="3 2"/></svg></div>
      <h3>Email Everywhere</h3>
      <p>Lorem ipsum dolor sit amet, consectetur adipisicing elit, sed do eiusmod tempor incididunt.Lorem ipsum dolor sit amet, consectetur</p>
      <span class="more">Read More +</span>
    </div>
    <div class="hero-card">
      <div class="ring"><svg width="40" height="36" viewBox="0 0 40 36"><g fill="none" stroke="#222" stroke-width="2"><path d="M11 2l3 6 6 1-4.5 4 1 6-5.5-3-5.5 3 1-6L2 9l6-1z"/><path d="M29 2l3 6 6 1-4.5 4 1 6-5.5-3-5.5 3 1-6L20 9l6-1z"/><path d="M11 18l3 6 6 1-4.5 4 1 6-5.5-3-5.5 3 1-6L2 25l6-1z"/><path d="M29 18l3 6 6 1-4.5 4 1 6-5.5-3-5.5 3 1-6L20 25l6-1z"/></g></svg></div>
      <h3>CRM Solutions</h3>
      <p>Lorem ipsum dolor sit amet, consectetur adipisicing elit, sed do eiusmod tempor incididunt.Lorem ipsum dolor sit amet, consectetur</p>
      <span class="more">Read More +</span>
    </div>
  </div>
  <div class="abs dots"><i></i><i></i><i></i></div>
</section>

<section class="welcome">
  <h1 class="abs title welcome-title">Welcome To Vale Linebacker</h1>
  <p class="abs welcome-text">Lorem ipsum dolor sit amet, consectetuer adipiscing elit, sed diam nonummy nibh euismod tincidunt ut laoreet dolore magna aliquam erat volutpat. Ut wisi enim ad minim veniam, quis nostrud exerci tation ullamcorper suscipit lobortis nisl ut aliquip ex ea commodo consequat. Lorem ipsum dolor sit amet, consectetuer adipiscing elit, sed diam nonummy nibh euismod tincidunt ut laoreet dolore magna aliquam erat volutpat. Ut wisi enim ad minim veniam, quis nostrud exerci tation ullamcorper suscipit lobortis nisl ut aliquip ex ea commodo consequat. Lorem ipsum dolor sit amet, consectetuer adipiscing elit, sed diam nonummy nibh euismod tincidunt ut laoreet dolore magna aliquam erat volutpat. Ut wisi enim ad minim veniam, quis nostrud exerci tation ullamcorper suscipit lobortis nisl ut aliquip ex ea commodo consequat.</p>
  <div class="abs btn" style="left:530px;top:810px">Read more +</div>
</section>

<section>
  <div class="abs band"></div>
  <h2 class="abs title what-title">What We Do</h2>
  <p class="abs what-text">We challenge the status quo by providing unique insights, emerging strategies and proven best practices. Our unwavering focus is on customer satisfaction. Our services include:</p>
  <ul class="abs checks">
    <li><svg width="15" height="12" viewBox="0 0 15 12"><path d="M1 6l4 4 9-9" fill="none" stroke="#4b9c2f" stroke-width="3"/></svg>Strategy</li>
    <li><svg width="15" height="12" viewBox="0 0 15 12"><path d="M1 6l4 4 9-9" fill="none" stroke="#4b9c2f" stroke-width="3"/></svg>Migration</li>
    <li><svg width="15" height="12" viewBox="0 0 15 12"><path d="M1 6l4 4 9-9" fill="none" stroke="#4b9c2f" stroke-width="3"/></svg>Implementation</li>
    <li><svg width="15" height="12" viewBox="0 0 15 12"><path d="M1 6l4 4 9-9" fill="none" stroke="#4b9c2f" stroke-width="3"/></svg>Integration</li>
    <li><svg width="15" height="12" viewBox="0 0 15 12"><path d="M1 6l4 4 9-9" fill="none" stroke="#4b9c2f" stroke-width="3"/></svg>Adoption and change management</li>
  </ul>
  <div class="abs laptop">
    <svg class="laptop-screen" viewBox="0 0 398 188">
      <line x1="30" y1="18" x2="30" y2="168" stroke="#bbb"/>
      <line x1="30" y1="168" x2="380" y2="168" stroke="#bbb"/>
      <g fill="var(--teal)">
        <rect x="42" y="88" width="10" height="80"/><rect x="57" y="76" width="10" height="92"/><rect x="72" y="80" width="10" height="88"/>
        <rect x="87" y="68" width="10" height="100"/><rect x="102" y="60" width="10" height="108"/><rect x="117" y="70" width="10" height="98"/>
        <rect x="132" y="78" width="10" height="90"/><rect x="147" y="112" width="10" height="56"/><rect x="162" y="118" width="10" height="50"/>
        <rect x="177" y="106" width="10" height="62"/><rect x="192" y="100" width="10" height="68"/><rect x="207" y="94" width="10" height="74"/>
        <rect x="222" y="86" width="10" height="82"/><rect x="237" y="72" width="10" height="96"/><rect x="252" y="60" width="10" height="108"/>
        <rect x="267" y="48" width="10" height="120"/><rect x="282" y="54" width="10" height="114"/><rect x="297" y="62" width="10" height="106"/>
        <rect x="312" y="70" width="10" height="98"/><rect x="327" y="76" width="10" height="92"/>
      </g>
      <polyline points="47,118 77,98 107,84 137,96 167,118 197,112 227,98 257,82 287,84 317,92 332,102" fill="none" stroke="#d9534f" stroke-width="1.2"/>
    </svg>
  </div>
</section>

<section>
  <h2 class="abs title services-title">Services</h2>
  <p class="abs services-sub">Lorem ipsum dolor sit amet, consectetuer adipiscing elit, sed diam nonummy nibh euismod tincidunt ut laoreet dolore magna aliquam erat</p>
  <div class="abs service" style="left:292px">
    <svg width="114" height="120" viewBox="0 0 114 120"><polygon points="57,2 110,31 110,89 57,118 4,89 4,31" fill="#ddd"/><polygon points="57,10 103,35 103,85 57,110 11,85 11,35" fill="var(--blue)"/><circle cx="57" cy="60" r="13" fill="none" stroke="#fff" stroke-width="3"/></svg>
    <h4>Gleamwork</h4>
    <p>It has survived not only five centuries, but also the leap into electronic typesetting, remaining. It was popularised.</p>
    <span class="more">Read More +</span>
  </div>
  <div class="abs service" style="left:497px">
    <svg width="114" height="120" viewBox="0 0 114 120"><polygon points="57,2 110,31 110,89 57,118 4,89 4,31" fill="#ddd"/><polygon points="57,10 103,35 103,85 57,110 11,85 11,35" fill="var(--blue)"/><rect x="40" y="46" width="34" height="24" fill="none" stroke="#fff" stroke-width="3"/><path d="M50 76h14M57 70v6M48 64l16-14" stroke="#fff" stroke-width="3"/></svg>
    <h4>Deployment</h4>
    <p>It has survived not only five centuries, but also the leap into electronic typesetting, remaining. It was popularised.</p>
    <span class="more">Read More +</span>
  </div>
  <div class="abs service" style="left:697px">
    <svg width="114" height="120" viewBox="0 0 114 120"><polygon points="57,2 110,31 110,89 57,118 4,89 4,31" fill="#ddd"/><polygon points="57,10 103,35 103,85 57,110 11,85 11,35" fill="var(--blue)"/><g fill="none" stroke="#fff" stroke-width="2.5"><ellipse cx="57" cy="46" rx="12" ry="5"/><path d="M45 46v28c0 3 5 5 12 5s12-2 12-5V46M45 55c0 3 5 5 12 5s12-2 12-5M45 65c0 3 5 5 12 5s12-2 12-5"/></g></svg>
    <h4>Migration</h4>
    <p>It has survived not only five centuries, but also the leap into electronic typesetting, remaining. It was popularised.</p>
    <span class="more">Read More +</span>
  </div>
  <div class="abs service" style="left:905px">
    <svg width="114" height="120" viewBox="0 0 114 120"><polygon points="57,2 110,31 110,89 57,118 4,89 4,31" fill="#ddd"/><polygon points="57,10 103,35 103,85 57,110 11,85 11,35" fill="var(--blue)"/><rect x="42" y="44" width="30" height="20" fill="#fff"/><path d="M36 68h42M57 68v8M44 78h26" stroke="#fff" stroke-width="3"/></svg>
    <h4>Project management</h4>
    <p>It has survived not only five centuries, but also the leap into electronic typesetting, remaining. It was popularised.</p>
    <span class="more">Read More +</span>
  </div>
  <div class="abs btn" style="left:530px;top:1540px">View More +</div>
</section>

<section>
  <div class="abs video" role="img" aria-label="Video player showing a story running chart presentation"></div>
  <h3 class="abs testi-title">Testmonials</h3>
  <div class="abs tarrow" style="left:948px"><svg width="7" height="10" viewBox="0 0 7 10"><path d="M6 1 2 5l4 4" fill="none" stroke="#777" stroke-width="1.6"/></svg></div>
  <div class="abs tarrow" style="left:976px"><svg width="7" height="10" viewBox="0 0 7 10"><path d="M1 1l4 4-4 4" fill="none" stroke="#777" stroke-width="1.6"/></svg></div>
  <div class="abs testi"></div>
  <div class="abs avatar" role="img" aria-label="Portrait photo of the reviewer"></div>
  <div class="abs tname">John Doe</div>
  <div class="abs trole">Project Manager</div>
  <div class="abs qmark">&ldquo;</div>
  <p class="abs quote">Nulla ultricies ornare erat, a rutrum lacus varius nec. Pellentesque vehicula lobortis dignissim. Ut scelerisque auctor eros sed porttitor. Nullam pulvinar ultrices malesuada.</p>
</section>

<footer>
  <div class="abs footer"></div>
  <div class="abs fcol" style="left:200px"><h5>About us</h5><p>Lorem ipsum dolor sit amet, consec-tetur adipiscing elit. Nulla convallis egestas rhoncus. Donec facilisis fermentum sem, ac viverra ante</p></div>
  <div class="abs fdiv" style="left:397px"></div>
  <div class="abs fcol" style="left:420px"><h5>Products</h5><ul><li>Network &amp; Convergence Services</li><li>Infrastructure SecurityServices</li><li>Enterprise Computing Services</li></ul></div>
  <div class="abs fdiv" style="left:608px"></div>
  <div class="abs fcol" style="left:630px"><h5>Industries</h5><ul><li>Architecture</li><li>Financial Services</li><li>Housing Associations</li><li>Non-profit</li><li>Retails</li></ul></div>
  <div class="abs fdiv" style="left:820px"></div>
  <div class="abs fcol" style="left:890px"><h5>Follow us</h5></div>
  <div class="abs social"><i style="background:#3b5a9a"></i><i style="background:#3fa7d9"></i><i style="background:#c6402f"></i><i style="background:#c8232c"></i><i style="background:#eee"></i></div>
  <div class="abs copyright">Copy right@ Vale Linebacker. 2014</div>
</footer>
</body>
</html>
```